Meridale Partners Website

Meridale Partners (MP) provide Analytics & Enterprise Performance Management (EPM) advisory & consultancy services. We are passionate about data and making a difference for our clients by working in partnership with them, helping them on their journey to becoming an Meridale Partner. We deliver insights which give our clients a competitive edge and a much deeper understanding of their organisation.

We need a website which shows who we are, what we do and how we do it.

www.meridale-partners.example is our very basic website at the moment. We want to completely revamp it with a corporate look

```html
<!DOCTYPE html>
<html lang="en">
<head>
<meta charset="utf-8">
<title>Meridale Partners</title>
<link href="https://fonts.googleapis.com/css2?family=Poppins:wght@300;400;500;600;700&display=swap" rel="stylesheet">
<style>
:root{
  --navy:#1f4661;
  --navy-deep:#163448;
  --navy-dark:#12293a;
  --steel:#3f7d9e;
  --orange:#e3863f;
  --orange-soft:#f0b487;
  --text:#5b6670;
  --line:#e3e6ea;
  --white:#fff;
}
*{margin:0;padding:0;box-sizing:border-box}
html,body{width:1200px;height:3712px;overflow:hidden}
body{position:relative;font-family:'Poppins',sans-serif;background:var(--white);color:var(--text)}
.abs{position:absolute}
.btn{position:absolute;background:var(--orange);color:#fff;font-weight:600;font-size:15px;letter-spacing:.5px;border-radius:6px;display:flex;align-items:center;justify-content:center}
.eyebrow{position:absolute;color:var(--orange);font-size:14px;letter-spacing:.5px;text-transform:uppercase}

/* header */
.header{position:absolute;left:0;top:0;width:1200px;height:70px;background:#fff;z-index:3}
.brand{position:absolute;display:flex;align-items:center;gap:12px}
.brand-dot{width:48px;height:48px;border-radius:50%;background:var(--navy)}
.brand-name{color:var(--navy);font-weight:600;line-height:1.05;text-transform:uppercase}
.nav{position:absolute;left:763px;top:27px;display:flex;gap:24px;font-size:13px;color:#333}
.nav .active{color:var(--orange);position:relative}
.nav .active::after{content:"";position:absolute;left:50%;top:33px;margin-left:-7px;border:7px solid transparent;border-bottom-color:var(--orange)}
.social{position:absolute;width:38px;height:38px;border-radius:50%;background:var(--orange)}

/* hero */
.hero-svg{position:absolute;left:0;top:70px}
.hero-title{position:absolute;left:698px;top:218px;font-size:54px;line-height:56px;font-weight:500;color:transparent;-webkit-text-stroke:1.5px #fff;letter-spacing:1px}
.hero-copy{position:absolute;left:699px;top:342px;width:440px;color:#fff;font-size:14px;line-height:23px;font-weight:300}

/* about */
.photo{position:absolute}
.about-title{position:absolute;left:632px;top:840px;color:var(--navy);font-size:32px;line-height:37px;font-weight:600}
.about-copy{position:absolute;left:634px;width:390px;font-size:12.5px;line-height:24px;font-weight:300}

/* services */
.svc-circle{position:absolute;border-radius:50%;border:6px solid #fff;color:#fff;text-align:center;display:flex;flex-direction:column;align-items:center;justify-content:center}
.svc-circle h3{font-size:16px;font-weight:600;margin:10px 0 6px;letter-spacing:.3px}
.svc-circle p{font-size:11.5px;line-height:19px;font-weight:300;width:72%}
.how-title{position:absolute;left:0;width:1200px;top:1690px;text-align:center;color:#fff;font-size:25px;line-height:34px;font-weight:600}
.card{position:absolute;top:1833px;width:299px;height:298px;background:#234c66;border-radius:8px;overflow:hidden;text-align:center;color:#fff;border:4px solid #2c5875}
.card .pic{height:172px}
.card h4{font-size:15px;font-weight:600;margin-top:18px;letter-spacing:.4px}
.card p{font-size:11.5px;line-height:19px;font-weight:300;width:82%;margin:8px auto 0}

/* insight */
.insight-title{position:absolute;left:137px;top:2334px;color:var(--navy);font-size:32px;font-weight:600}
.post{position:absolute;left:135px;width:513px;height:96px}
.post .thumb{position:absolute;left:0;top:0;width:93px;height:93px;border-radius:4px}
.post .date{position:absolute;left:119px;top:0;color:var(--orange);font-size:11.5px}
.post h5{position:absolute;left:119px;top:20px;color:var(--navy);font-size:16px;font-weight:600}
.post p{position:absolute;left:119px;top:48px;width:290px;font-size:11.5px;line-height:20px;font-weight:300}
.post .go{position:absolute;left:454px;top:31px;width:40px;height:40px}
.rule{position:absolute;left:135px;width:513px;height:1px;background:var(--line)}

/* contact */
.contact-title{position:absolute;left:0;width:1200px;top:2980px;text-align:center;color:#fff;font-size:34px;font-weight:600;letter-spacing:.5px}
.contact-sub{position:absolute;left:0;width:1200px;top:3027px;text-align:center;color:#fff;font-size:14px}
.info{position:absolute;left:135px;display:flex;align-items:flex-start;gap:16px;color:#fff;font-size:12px;line-height:20px;font-weight:300}
.info svg{flex:none}
.field{position:absolute;background:#fff;border-radius:4px;box-shadow:3px 0 0 var(--orange);font-size:11.5px;color:#888;padding:11px 13px}

/* footer */
.foot-h{position:absolute;top:3444px;color:var(--navy);font-size:16px;font-weight:600;letter-spacing:.4px}
.foot-list{position:absolute;top:3480px;list-style:none;font-size:11.5px;line-height:26px;color:var(--text)}
.foot-list li::before{content:"";display:inline-block;width:5px;height:5px;border-radius:50%;background:var(--orange);margin-right:11px;vertical-align:middle}
.foot-contact{position:absolute;left:887px;display:flex;gap:14px;font-size:11.5px;line-height:21px;color:var(--text)}
.copyright{position:absolute;left:0;width:1200px;top:3665px;text-align:center;font-size:11px;color:#444}
</style>
</head>
<body>

<header class="header">
  <div class="brand" style="left:58px;top:11px">
    <span class="brand-dot"></span>
    <span class="brand-name" style="font-size:17px">Meridale<br>Partners</span>
  </div>
  <nav class="nav">
    <span class="active">Home</span><span>Services</span><span>About Us</span><span>Contact Us</span>
  </nav>
  <span class="social" style="left:1062px;top:17px"></span>
  <span class="social" style="left:1102px;top:17px"></span>
</header>

<svg class="hero-svg" width="1200" height="680" viewBox="0 0 1200 680">
  <defs>
    <linearGradient id="heroPhoto" x1="0" y1="0" x2="1" y2="1">
      <stop offset="0" stop-color="#2a5a74"/>
      <stop offset=".5" stop-color="#1c4259"/>
      <stop offset="1" stop-color="#2f6a82"/>
    </linearGradient>
  </defs>
  <path d="M0 440 L0 525 C160 640 360 670 580 665 C720 662 830 645 905 620 L905 560 Z" fill="var(--orange)"/>
  <path role="img" aria-label="Photo of two analysts studying charts on a large screen" d="M0 0 H1200 V455 C1000 580 760 640 540 625 C320 610 130 545 0 445 Z" fill="url(#heroPhoto)"/>
</svg>
<div class="hero-title">MERIDALE<br>PARTNERS</div>
<p class="hero-copy">We are passionate about data and making a difference for our clients by working in partnership with them, helping them on their Journey to becoming an Meridale Partner</p>
<div class="btn" style="left:698px;top:420px;width:151px;height:40px">LEARN MORE</div>

<!-- who we are -->
<div class="photo" style="left:130px;top:806px;width:170px;height:178px;background:#fbe9dc" role="img" aria-label="Decorative dotted pattern"></div>
<div class="photo" role="img" aria-label="Photo of a team meeting in a bright office" style="left:158px;top:847px;width:293px;height:285px;background:linear-gradient(135deg,#dfe5ea,#9aa7b3);border-radius:4px"></div>
<div class="photo" role="img" aria-label="Photo of hands typing on a laptop showing charts" style="left:370px;top:985px;width:179px;height:194px;background:linear-gradient(135deg,#5c6f80,#25323e);border:5px solid #fff;border-radius:10px"></div>
<div class="eyebrow" style="left:635px;top:809px">Who we are</div>
<h2 class="about-title">MERIDALE<br>PARTNERS</h2>
<p class="about-copy" style="top:924px">MP are a Data Analytics &amp; EPM company, specialising in the implementation and support of Business Intelligence, EPM and Data Analytics business solutions, both in the Cloud and on-premise</p>
<p class="about-copy" style="top:1034px">Meridale Partners is an exciting start-up in the Data Analytics and EPM space. Founded in 2019, MP specialise in the implementation and support of BI, EPM and Data Analytics business solutions, both in the Cloud and on-premise.</p>
<div class="btn" style="left:631px;top:1143px;width:145px;height:40px">LEARN MORE</div>

<!-- services band -->
<svg class="abs" style="left:0;top:1420px" width="1200" height="860" viewBox="0 0 1200 860">
  <defs>
    <linearGradient id="band" x1="0" y1="0" x2="0" y2="1">
      <stop offset="0" stop-color="#1d4259"/>
      <stop offset="1" stop-color="#163448"/>
    </linearGradient>
  </defs>
  <path d="M0 172 Q600 -160 1200 160 V726 Q600 940 0 726 Z" fill="url(#band)"/>
</svg>

<div class="svc-circle" style="left:153px;top:1316px;width:262px;height:262px;background:linear-gradient(160deg,#4a8bab,#326a88)">
  <svg width="62" height="58" viewBox="0 0 62 58" fill="none" stroke="#fff" stroke-width="2"><rect x="2" y="2" width="58" height="40" rx="2"/><path d="M22 42v8M40 42v8M14 54h34M12 34V24M20 34V16M28 34V22M36 34V14M44 34V20M52 34V26"/></svg>
  <h3>ADVISE &amp; ARCHITECT</h3>
  <p>Helping our customers understand the art of the possible.</p>
</div>
<div class="svc-circle" style="left:453px;top:1280px;width:292px;height:292px;background:linear-gradient(160deg,#e6904b,#d9773a)">
  <svg width="64" height="62" viewBox="0 0 64 62" fill="none" stroke="#fff" stroke-width="2"><circle cx="32" cy="26" r="7"/><circle cx="32" cy="26" r="13" stroke-dasharray="5 4"/><path d="M2 46h12l10 4h12l16-10M2 58h16l26-4 18-14"/></svg>
  <h3>DESIGN &amp; IMPLEMENT</h3>
  <p>Working with the project management team, through each stage of the project, with clearly defined deliverables and well exercised plans to deliver them.</p>
</div>
<div class="svc-circle" style="left:783px;top:1316px;width:262px;height:262px;background:linear-gradient(160deg,#4a8bab,#326a88)">
  <svg width="60" height="60" viewBox="0 0 60 60" fill="none" stroke="#fff" stroke-width="2"><rect x="2" y="2" width="56" height="56" rx="3"/><path d="M2 12h56"/><circle cx="22" cy="32" r="8"/><circle cx="22" cy="32" r="3"/><circle cx="40" cy="44" r="7"/><circle cx="40" cy="44" r="2.5"/></svg>
  <h3>OPTIMSE &amp; MANAGE</h3>
  <p>Our Managed Services delivers proactive, on-demand support for EPM and Data.</p>
</div>

<div class="eyebrow" style="left:0;width:1200px;text-align:center;top:1656px">How we do it</div>
<h2 class="how-title">We Provide Analytics &amp; Enterprise<br>Performance Management (EPM) Advisory &amp;<br>Consultancy Services</h2>

<div class="card" style="left:135px">
  <div class="pic" role="img" aria-label="Photo of an analyst pointing at a glass board of charts" style="background:linear-gradient(135deg,#2d5a7c,#0f2233)"></div>
  <h4>ANALYTICS</h4>
  <p>Lorem Ipsum has been the industry's standard dummy text ever since the when an unknown printer</p>
</div>
<div class="card" style="left:451px">
  <div class="pic" role="img" aria-label="Photo of a team discussing around a meeting table" style="background:linear-gradient(135deg,#a8a39a,#4e4a45)"></div>
  <h4>CONSULTANCY</h4>
  <p>Lorem Ipsum has been the industry's standard dummy text ever since the when an unknown printer</p>
</div>
<div class="card" style="left:766px">
  <div class="pic" role="img" aria-label="Photo of colleagues reviewing reports on tablets" style="background:linear-gradient(135deg,#6d7378,#23282c)"></div>
  <h4>ADVISORY</h4>
  <p>Lorem Ipsum has been the industry's standard dummy text ever since the when an unknown printer</p>
</div>

<!-- insight -->
<div class="eyebrow" style="left:137px;top:2308px">Know more</div>
<h2 class="insight-title">INSIGHT</h2>

<div class="post" style="top:2398px">
  <div class="thumb" role="img" aria-label="Photo of two colleagues at a whiteboard" style="background:linear-gradient(135deg,#b9c6cf,#4d6272)"></div>
  <span class="date">September 01, 2022</span>
  <h5>Meridale Partner Journey</h5>
  <p>Lorem Ipsum has been the industry's standard dummy text ever since the when.</p>
  <svg class="go" viewBox="0 0 40 40" fill="none" stroke="var(--orange)" stroke-width="1.5"><circle cx="20" cy="20" r="19"/><path d="M12 20h16M22 14l6 6-6 6"/></svg>
</div>
<div class="rule" style="top:2519px"></div>
<div class="post" style="top:2537px">
  <div class="thumb" role="img" aria-label="Image of a hand touching a digital network" style="background:linear-gradient(135deg,#3e77b5,#102b57)"></div>
  <span class="date">September 01, 2022</span>
  <h5>Meridale Partner Journey</h5>
  <p>Lorem Ipsum has been the industry's standard text ever since the when an printer.</p>
  <svg class="go" viewBox="0 0 40 40" fill="none" stroke="var(--orange)" stroke-width="1.5"><circle cx="20" cy="20" r="19"/><path d="M12 20h16M22 14l6 6-6 6"/></svg>
</div>
<div class="rule" style="top:2654px"></div>
<div class="post" style="top:2674px">
  <div class="thumb" role="img" aria-label="Photo of an office with people working" style="background:linear-gradient(135deg,#a9a79f,#4f4b45)"></div>
  <span class="date">September 01, 2022</span>
  <h5>Meridale Partner Journey</h5>
  <p>Lorem Ipsum has been the industry's standard text ever since the when an printer.</p>
  <svg class="go" viewBox="0 0 40 40" fill="none" stroke="var(--orange)" stroke-width="1.5"><circle cx="20" cy="20" r="19"/><path d="M12 20h16M22 14l6 6-6 6"/></svg>
</div>

<svg class="abs" style="left:700px;top:2310px" width="490" height="500" viewBox="0 0 490 500">
  <rect x="20" y="20" width="150" height="150" transform="rotate(45 95 95) translate(20 60)" fill="#f6ddcb" role="img" aria-label="Decorative dotted pattern"/>
  <rect x="330" y="330" width="110" height="110" transform="rotate(45 385 385)" fill="#dfe5ea" role="img" aria-label="Decorative dotted pattern"/>
  <path d="M95 230 A199 199 0 0 1 420 110 M445 160 A199 199 0 0 1 430 390" fill="none" stroke="var(--orange)" stroke-width="3"/>
  <circle cx="252" cy="268" r="187" fill="#fff"/>
  <circle role="img" aria-label="Photo of a business discussion between colleagues" cx="252" cy="268" r="187" fill="url(#insightPhoto)"/>
  <defs>
    <radialGradient id="insightPhoto" cx=".6" cy=".3" r=".8">
      <stop offset="0" stop-color="#c98a5c"/>
      <stop offset=".5" stop-color="#5e4a40"/>
      <stop offset="1" stop-color="#22201f"/>
    </radialGradient>
  </defs>
</svg>

<!-- contact -->
<svg class="abs" style="left:0;top:2800px" width="1200" height="600" viewBox="0 0 1200 600">
  <defs>
    <linearGradient id="contactBg" x1="0" y1="0" x2="1" y2="1">
      <stop offset="0" stop-color="#24506b"/>
      <stop offset="1" stop-color="#173a52"/>
    </linearGradient>
  </defs>
  <path d="M300 92 Q720 -75 1200 120 L1200 190 Q750 -27.5 300 92 Z" fill="var(--orange)"/>
  <path d="M0 210 Q600 -100 1200 190 V600 H0 Z" fill="url(#contactBg)"/>
</svg>
<div class="eyebrow" style="left:0;width:1200px;text-align:center;top:2952px">Contact us</div>
<h2 class="contact-title">HAVE ANY QUESTION?</h2>
<p class="contact-sub">Contact Us To Discuss Your Business Needs</p>

<div class="info" style="top:3098px">
  <svg width="40" height="40" viewBox="0 0 40 40"><circle cx="20" cy="20" r="20" fill="var(--orange)"/><path d="M20 10a7 7 0 0 0-7 7c0 5 7 13 7 13s7-8 7-13a7 7 0 0 0-7-7z" fill="#fff"/><circle cx="20" cy="17" r="2.5" fill="var(--orange)"/></svg>
  <span>MERIDALE PARTNERS<br>14 Harbour Row, Eastvale,<br>Dublin 8, D08 XR21</span>
</div>
<div class="info" style="top:3180px;align-items:center">
  <svg width="40" height="40" viewBox="0 0 40 40"><circle cx="20" cy="20" r="20" fill="var(--orange)"/><path d="M14 11l4 5-2 3c1 3 3 5 6 6l3-2 5 4-2 3c-8 1-17-8-16-16z" fill="#fff"/></svg>
  <span>01 555 0142</span>
</div>
<div class="info" style="top:3236px;align-items:center">
  <svg width="40" height="40" viewBox="0 0 40 40"><circle cx="20" cy="20" r="20" fill="var(--orange)"/><rect x="11" y="13" width="18" height="14" rx="1" fill="#fff"/><path d="M11 14l9 7 9-7" fill="none" stroke="var(--orange)" stroke-width="1.5"/></svg>
  <span>info@meridale-partners.example</span>
</div>

<div class="field" style="left:451px;top:3103px;width:260px;height:41px">Name *</div>
<div class="field" style="left:723px;top:3103px;width:262px;height:41px">Email *</div>
<div class="field" style="left:451px;top:3155px;width:260px;height:41px">Phone *</div>
<div class="field" style="left:723px;top:3155px;width:262px;height:41px">Services*</div>
<div class="field" style="left:451px;top:3210px;width:534px;height:58px">Message *</div>
<div class="btn" style="left:451px;top:3283px;width:99px;height:39px;font-size:14px">SUBMIT</div>

<!-- footer -->
<div class="brand" style="left:75px;top:3455px">
  <span class="brand-dot" style="width:58px;height:58px"></span>
  <span class="brand-name" style="font-size:20px">Meridale<br>Partners</span>
</div>
<span class="social" style="left:145px;top:3525px"></span>
<span class="social" style="left:193px;top:3525px"></span>

<h6 class="foot-h" style="left:337px">SITEMAP</h6>
<ul class="foot-list" style="left:337px"><li>Home</li><li>About Us</li><li>Services</li><li>Contact Us</li></ul>
<h6 class="foot-h" style="left:612px">SERVICES</h6>
<ul class="foot-list" style="left:612px"><li>Advise &amp; Architect</li><li>Design &amp; Implement</li><li>Optimse &amp; Manage</li></ul>
<h6 class="foot-h" style="left:887px">CONTACT US</h6>
<div class="foot-contact" style="top:3482px">
  <svg width="16" height="22" viewBox="0 0 16 22"><path d="M8 1a7 7 0 0 0-7 7c0 5 7 13 7 13s7-8 7-13a7 7 0 0 0-7-7z" fill="var(--orange)"/><circle cx="8" cy="8" r="2.5" fill="#fff"/></svg>
  <span>14 Harbour Row, Eastvale,<br>Dublin 8, D08 XR21</span>
</div>
<div class="foot-contact" style="top:3532px">
  <svg width="16" height="18" viewBox="0 0 16 18"><path d="M2 1l4 5-2 3c1 3 3 5 6 6l3-2 3 4-2 2C7 19-2 9 2 1z" fill="var(--orange)"/></svg>
  <span>01 555 0142</span>
</div>
<div class="foot-contact" style="top:3562px">
  <svg width="16" height="14" viewBox="0 0 16 14"><rect x="0" y="1" width="16" height="12" rx="1" fill="var(--orange)"/><path d="M1 2l7 6 7-6" fill="none" stroke="#fff" stroke-width="1.3"/></svg>
  <span>info@meridale-partners.example</span>
</div>

<div class="abs" style="left:58px;top:3633px;width:440px;height:1px;background:var(--line)"></div>
<div class="abs" style="left:702px;top:3633px;width:436px;height:1px;background:var(--line)"></div>
<div class="abs" style="left:520px;top:3614px;width:160px;height:38px;border-radius:4px;background:#f3e3d8" aria-label="Partner badge" role="img"></div>

<p class="copyright">©MERIDALE PARTNERS &nbsp;- 2022 All rights reserved.</p>

</body>
</html>
```